Quran Jar

So I need help designing bespoke jars which will contain religious quotes.

So there will be three jars in total sold either individually or in two or as a three.

Each Jar will have different contents and preferably a different colour scheme.

I want the packaging to be customised with my branding and logo and to make the product stand out I am thinking of packing it further in a cotton bag with my branding.

```html
<!DOCTYPE html>
<html lang="en">
<head>
<meta charset="utf-8">
<title>Serene Verses – Jar Packaging Lids</title>
<link rel="stylesheet" href="https://fonts.googleapis.com/css2?family=Montserrat:wght@300;400;600&display=swap">
<style>
  :root {
    --stage: #e4e5e4;
    --green: #41604d;
    --green-light: #5a8569;
    --gold: #8b7436;
    --gold-light: #b39b4c;
    --gold-pale: #d8c27a;
    --white: #f7f7f5;
  }
  html, body {
    margin: 0;
    padding: 0;
    width: 1200px;
    height: 790px;
    overflow: hidden;
    background: var(--stage);
    font-family: "Montserrat", sans-serif;
  }
  .range {
    display: grid;
    grid-template-columns: 600px 600px;
    grid-template-rows: 395px 395px;
    width: 1200px;
    height: 790px;
  }
  .range__cell {
    display: flex;
    align-items: center;
    justify-content: center;
  }
  .lid {
    position: relative;
    width: 440px;
    height: 290px;
    overflow: hidden;
    background: var(--lid-bg);
    box-shadow: 0 10px 24px rgba(0, 0, 0, 0.18);
  }
  .lid--green-gold { --lid-bg: var(--green); --lid-accent: var(--gold); --lid-dot: var(--gold); --lid-ink: var(--white); --lid-brand: var(--gold-pale); }
  .lid--green-white { --lid-bg: var(--green); --lid-accent: var(--white); --lid-dot: var(--white); --lid-ink: var(--white); --lid-brand: var(--gold-light); }
  .lid--gold-white { --lid-bg: var(--gold); --lid-accent: var(--white); --lid-dot: var(--white); --lid-ink: var(--white); --lid-brand: var(--gold-pale); }
  .lid--green-trio { --lid-bg: var(--green); --lid-accent: var(--gold); --lid-dot: var(--white); --lid-ink: var(--white); --lid-brand: var(--gold-pale); }
  .lid__art {
    position: absolute;
    inset: 0;
    width: 440px;
    height: 290px;
  }
  .lid__accent { fill: var(--lid-accent); }
  .lid__dot { fill: var(--lid-dot); }
  .brand {
    position: absolute;
    left: 30px;
    top: 26px;
    color: var(--lid-brand);
  }
  .brand__name {
    display: flex;
    align-items: center;
    gap: 6px;
    font-weight: 600;
    font-size: 15px;
    letter-spacing: 0.3px;
  }
  .brand__mark {
    width: 8px;
    height: 8px;
    border-radius: 50%;
    background: currentColor;
  }
  .brand__tagline {
    margin-top: 3px;
    font-weight: 400;
    font-size: 5px;
    letter-spacing: 2px;
    text-transform: uppercase;
  }
  .jars {
    position: absolute;
    right: 48px;
    top: 140px;
    display: flex;
    align-items: center;
    color: var(--lid-ink);
  }
  .jars__item {
    text-align: center;
    padding: 0 12px;
    line-height: 1;
  }
  .jars__item + .jars__item { border-left: 1px solid var(--lid-ink); }
  .jars__name {
    display: block;
    font-weight: 300;
    font-size: 15px;
    letter-spacing: 0.5px;
  }
  .jars__type {
    display: block;
    font-weight: 300;
    font-size: 6px;
    letter-spacing: 1px;
    margin-top: 2px;
  }
</style>
</head>
<body>
<main class="range">

  <section class="range__cell">
    <div class="lid lid--green-gold">
      <svg class="lid__art" viewBox="0 0 440 290" role="img" aria-label="Large gold emblem artwork of the jar range">
        <circle class="lid__accent" cx="70" cy="260" r="165"/>
        <circle class="lid__dot" cx="175" cy="70" r="14"/>
        <circle class="lid__dot" cx="350" cy="112" r="7"/>
        <rect class="lid__accent" x="120" y="268" width="330" height="6" rx="3" transform="rotate(-8 120 268)"/>
      </svg>
      <div class="brand">
        <div class="brand__name"><span class="brand__mark"></span>Serene Verses</div>
        <div class="brand__tagline">daily quotes of faith</div>
      </div>
      <div class="jars">
        <div class="jars__item"><span class="jars__name">QURAN</span><span class="jars__type">JAR</span></div>
        <div class="jars__item"><span class="jars__name">HADITH</span><span class="jars__type">JAR</span></div>
      </div>
    </div>
  </section>

  <section class="range__cell">
    <div class="lid lid--green-white">
      <svg class="lid__art" viewBox="0 0 440 290" role="img" aria-label="Large white emblem artwork of the jar range">
        <circle class="lid__accent" cx="70" cy="260" r="165"/>
        <circle class="lid__dot" cx="175" cy="70" r="14"/>
        <circle class="lid__dot" cx="350" cy="112" r="7"/>
        <rect class="lid__accent" x="120" y="268" width="330" height="6" rx="3" transform="rotate(-8 120 268)"/>
      </svg>
      <div class="brand">
        <div class="brand__name"><span class="brand__mark"></span>Serene Verses</div>
        <div class="brand__tagline">daily quotes of faith</div>
      </div>
      <div class="jars">
        <div class="jars__item"><span class="jars__name">QURAN</span><span class="jars__type">JAR</span></div>
        <div class="jars__item"><span class="jars__name">DUA</span><span class="jars__type">JAR</span></div>
      </div>
    </div>
  </section>

  <section class="range__cell">
    <div class="lid lid--gold-white">
      <svg class="lid__art" viewBox="0 0 440 290" role="img" aria-label="Large white emblem artwork of the jar range">
        <circle class="lid__accent" cx="70" cy="260" r="165"/>
        <circle class="lid__dot" cx="175" cy="70" r="14"/>
        <circle class="lid__dot" cx="350" cy="112" r="7"/>
        <rect class="lid__accent" x="120" y="268" width="330" height="6" rx="3" transform="rotate(-8 120 268)"/>
      </svg>
      <div class="brand">
        <div class="brand__name"><span class="brand__mark"></span>Serene Verses</div>
        <div class="brand__tagline">daily quotes of faith</div>
      </div>
      <div class="jars">
        <div class="jars__item"><span class="jars__name">HADITH</span><span class="jars__type">JAR</span></div>
        <div class="jars__item"><span class="jars__name">DUA</span><span class="jars__type">JAR</span></div>
      </div>
    </div>
  </section>

  <section class="range__cell">
    <div class="lid lid--green-trio">
      <svg class="lid__art" viewBox="0 0 440 290" role="img" aria-label="Large gold emblem artwork of the jar range">
        <circle class="lid__accent" cx="70" cy="260" r="165"/>
        <circle class="lid__dot" cx="175" cy="70" r="14"/>
        <circle class="lid__dot" cx="350" cy="112" r="7"/>
        <rect class="lid__accent" x="120" y="268" width="330" height="6" rx="3" transform="rotate(-8 120 268)"/>
      </svg>
      <div class="brand">
        <div class="brand__name"><span class="brand__mark"></span>Serene Verses</div>
        <div class="brand__tagline">daily quotes of faith</div>
      </div>
      <div class="jars">
        <div class="jars__item"><span class="jars__name">QURAN</span><span class="jars__type">JAR</span></div>
        <div class="jars__item"><span class="jars__name">HADITH</span><span class="jars__type">JAR</span></div>
        <div class="jars__item"><span class="jars__name">DUA</span><span class="jars__type">JAR</span></div>
      </div>
    </div>
  </section>

</main>
</body>
</html>
```